Design and Renovation Company Luxury Business Card

I want to create a luxury business card for a Design and Renovation Firm . We will use our current logo. The company name is 528BUILDA. We do not want anything standard. We need a very unique concept.
Please see uploaded inspiration. I really like the textured paper option. I would like the card to be thick with debossing, and/or embossing options. The logo has orange in it but I would like to see the card with and without the orange. I think the orange may make the company feel less high-end. The goal is to elevate the logo not match its vibe per se of the logo. We want something very unique, not standard at all!
I would like a space for :
Logo,
Name,
Position,
Email,
Office number,
Website Address,
Business Address,
Thank you!
Have fun!
Target Market(s)
Home owners Age 35 +
Industry/Entity Type
Design and Renovation
Contact Information for Business Card
Logo, Name, Position, Email, Office number, Website Address, Business Address,.
Colors
Designer to choose colors to be used in the design.
Requirements
Must have
- A luxury designer feel. Must be black or dark grey but open to other luxury ideas.
Nice to have
- Gold, silver, black embossing or debossing. Textured paper design.
Should not have
- A cheap look and feel.

```html
<!DOCTYPE html>
<html lang="en">
<head>
<meta charset="UTF-8">
<title>528BUILDA Business Card</title>
<link rel="stylesheet" href="https://fonts.googleapis.com/css2?family=Montserrat:wght@400;600;700&display=swap">
<style>
  :root {
    --backdrop: #9a9a9a;
    --card-white: #f7f7f5;
    --card-black: #1b1b1b;
    --accent-orange: #f08a1c;
    --edge-orange: #d9770f;
    --ink-dark: #2b2b2b;
    --emboss-grey: #7c7c7c;
    --tint-square: #f6e8d8;
  }
  * { box-sizing: border-box; margin: 0; padding: 0; }
  html, body {
    width: 1200px; height: 956px; overflow: hidden;
    background: var(--backdrop);
    font-family: "Montserrat", Arial, sans-serif;
  }
  .stage { position: relative; width: 1200px; height: 956px; }
  .card {
    position: absolute; left: 290px;
    width: 620px; height: 354px;
    border-bottom: 4px solid var(--edge-orange);
    box-shadow: 0 18px 40px rgba(0,0,0,0.28);
  }
  .card-front { top: 92px; background: var(--card-white); }
  .card-back { top: 506px; background: var(--card-black); }

  .front-content { position: absolute; left: 54px; top: 50px; width: 330px; }
  .person-name {
    color: var(--accent-orange); font-weight: 700; font-size: 24px;
    letter-spacing: 1px; line-height: 1.2;
  }
  .person-role { color: var(--ink-dark); font-size: 13px; margin-top: 2px; }
  .rule {
    height: 0; border-top: 1.5px solid var(--accent-orange);
    margin: 16px 0; width: 290px;
  }
  .address { color: var(--ink-dark); font-size: 13px; line-height: 1.4; }
  .contact-list { list-style: none; }
  .contact-list li {
    display: flex; align-items: center; gap: 10px;
    color: var(--ink-dark); font-size: 13px; line-height: 1.7;
  }
  .contact-list svg { width: 12px; height: 12px; fill: var(--accent-orange); flex: none; }
  .accent-square {
    position: absolute; right: 64px; top: 118px;
    width: 150px; height: 150px; background: var(--tint-square);
  }

  .brand-name {
    position: absolute; left: 0; right: 0; top: 148px;
    text-align: center;
    color: var(--emboss-grey); font-weight: 600; font-size: 52px;
    letter-spacing: 3px; line-height: 1;
  }
</style>
</head>
<body>
<main class="stage">
  <section class="card card-front">
    <div class="front-content">
      <h1 class="person-name">DANIEL HARTLEY</h1>
      <p class="person-role">Medical Director</p>
      <div class="rule"></div>
      <p class="address">412 Harbor View Lane Suite 18<br>Oakridge, New York 10583</p>
      <div class="rule"></div>
      <ul class="contact-list">
        <li><svg viewBox="0 0 24 24" aria-hidden="true"><path d="M6.6 10.8a15 15 0 0 0 6.6 6.6l2.2-2.2a1 1 0 0 1 1-.25 11.4 11.4 0 0 0 3.6.57 1 1 0 0 1 1 1V20a1 1 0 0 1-1 1A17 17 0 0 1 3 4a1 1 0 0 1 1-1h3.5a1 1 0 0 1 1 1c0 1.250.2 2.45.57 3.57a1 1 0 0 1-.25 1z"/></svg>(000)555-2190</li>
        <li><svg viewBox="0 0 24 24" aria-hidden="true"><path d="M2 5h20v14H2z M4 7v.4l8 5 8-5V7l-8 5z" fill-rule="evenodd"/></svg>hello@528builda.com</li>
        <li><svg viewBox="0 0 24 24" aria-hidden="true"><circle cx="12" cy="12" r="10"/></svg>www.528builda.com</li>
      </ul>
    </div>
    <div class="accent-square"></div>
  </section>

  <section class="card card-back">
    <p class="brand-name">528BUILDA</p>
  </section>
</main>
</body>
</html>
```